Harrow Hide Revival Product Label

We need a design for a label to be used on bottles of leather cleaner and conditioner products that will be used in curated kits. We would like it to incorporate our business logo as well as have an area that we can fill in later with the appropriate product name as needed. We would like to see designs that use shades of brown, but we are open to other colors often seen in leather. I am including the Harrow Hide business Logo below, however again we would prefer to have the label in various shades of browns, rather than the red and grey, more like the mock-up that I am also attaching.

*** I am attaching examples of the types of bottles that will be used. They vary in size from 8 oz to 16 oz. if you are designing a label for a spray bottle they are from 16-32 oz. ***

```html
<!DOCTYPE html>
<html lang="en">
<head>
<meta charset="utf-8">
<title>Harrow Hide Revival – Leather Cleaner &amp; Conditioner Label</title>
<link rel="stylesheet" href="https://fonts.googleapis.com/css2?family=Montserrat:wght@600;800;900&family=Lexend:wght@700&display=swap">
<style>
  :root {
    --backdrop: #3a3a3c;
    --label-white: #ffffff;
    --label-mist: #e4e4e4;
    --charcoal: #333335;
    --maroon: #6a1419;
    --maroon-deep: #3e0d10;
    --maroon-bright: #7a161d;
    --gold-light: #f3dfa0;
    --gold: #c9a24a;
    --gold-dark: #7d5d1c;
    --seat-light: #b0714a;
    --seat-dark: #3c1e12;
  }
  html, body {
    margin: 0;
    padding: 0;
    width: 816px;
    height: 1200px;
    overflow: hidden;
    background: var(--backdrop);
  }
  .canvas {
    position: relative;
    width: 816px;
    height: 1200px;
  }
  .label {
    position: absolute;
    left: 203px;
    top: 36px;
    width: 410px;
    height: 1128px;
    box-shadow: 10px 12px 22px rgba(0,0,0,0.45);
  }
  .label svg { display: block; width: 100%; height: 100%; }
  .brand-name {
    font-family: "Montserrat", sans-serif;
    font-weight: 600;
    fill: var(--maroon);
  }
  .product-title {
    font-family: "Lexend", sans-serif;
    font-weight: 700;
  }
  .product-subtitle {
    font-family: "Montserrat", sans-serif;
    font-weight: 900;
    fill: var(--label-white);
  }
  .volume {
    font-family: "Montserrat", sans-serif;
    font-weight: 800;
    fill: var(--maroon);
  }
</style>
</head>
<body>
<main class="canvas">
  <section class="label" aria-label="Harrow Hide Revival leather cleaner and conditioner label">
    <svg viewBox="0 0 500 1375" xmlns="http://www.w3.org/2000/svg">
      <defs>
        <linearGradient id="mist-top" x1="0" y1="0" x2="1" y2="1">
          <stop offset="0" stop-color="var(--label-mist)"/>
          <stop offset="0.45" stop-color="var(--label-white)"/>
        </linearGradient>
        <linearGradient id="mist-bottom" x1="0" y1="0" x2="1" y2="1">
          <stop offset="0.5" stop-color="var(--label-white)"/>
          <stop offset="1" stop-color="var(--label-mist)"/>
        </linearGradient>
        <linearGradient id="band-fill" x1="0" y1="0" x2="1" y2="0">
          <stop offset="0" stop-color="var(--maroon-deep)"/>
          <stop offset="0.55" stop-color="var(--maroon)"/>
          <stop offset="1" stop-color="var(--maroon-bright)"/>
        </linearGradient>
        <radialGradient id="seat-photo" cx="0.45" cy="0.45" r="0.6">
          <stop offset="0" stop-color="var(--seat-light)"/>
          <stop offset="1" stop-color="var(--seat-dark)"/>
        </radialGradient>
        <linearGradient id="gold-fill" x1="0" y1="0" x2="0" y2="1">
          <stop offset="0" stop-color="var(--gold-light)"/>
          <stop offset="0.5" stop-color="var(--gold)"/>
          <stop offset="1" stop-color="var(--gold-dark)"/>
        </linearGradient>
        <clipPath id="label-edge">
          <rect x="0" y="0" width="500" height="1375"/>
        </clipPath>
      </defs>

      <g clip-path="url(#label-edge)">
        <rect class="label-ground" x="0" y="0" width="500" height="700" fill="url(#mist-top)"/>
        <rect class="label-ground" x="0" y="700" width="500" height="675" fill="url(#mist-bottom)"/>

        <!-- Maroon sweep band; its top edge sits hidden behind the photo window -->
        <path class="title-band" d="M0,640 L250,640 L500,770 L500,1088 C370,1160 190,1218 0,1232 Z" fill="url(#band-fill)"/>
        <path class="band-edge" d="M0,1232 C190,1218 370,1160 500,1088" fill="none" stroke="var(--charcoal)" stroke-width="11"/>

        <!-- Diagonal rule from top right, ending beside the brand mark -->
        <path class="diagonal-rule" d="M500,158 L192,300" fill="none" stroke="var(--charcoal)" stroke-width="11"/>

        <!-- Photo window -->
        <circle class="window-ring" cx="290" cy="595" r="278" fill="var(--charcoal)"/>
        <circle class="window-gap" cx="290" cy="595" r="266" fill="var(--label-white)"/>
        <circle class="window-photo" cx="290" cy="595" r="248" fill="url(#seat-photo)" role="img" aria-label="Photo of a car interior with tan leather seats, headrest pillows and lumbar cushion"/>

        <!-- Brand -->
        <circle class="brand-dot" cx="123" cy="275" r="44" fill="var(--maroon)"/>
        <text class="brand-name" x="180" y="268" font-size="27" transform="rotate(-24 180 268)">Harrow Hide Revival</text>

        <!-- Product name -->
        <g class="product" transform="rotate(-9 260 1060)">
          <text class="product-title" x="250" y="1020" font-size="112" text-anchor="middle" fill="url(#gold-fill)">Leather</text>
          <text class="product-subtitle" x="268" y="1066" font-size="40" text-anchor="middle">CLEANER &amp;</text>
          <text class="product-subtitle" x="268" y="1112" font-size="40" text-anchor="middle">CONDITIONER</text>
        </g>

        <text class="volume" x="251" y="1302" font-size="32" text-anchor="middle">16 oz</text>
      </g>
    </svg>
  </section>
</main>
</body>
</html>
```